Kestrel Facilities Business Card Design

We would now like to design business cards with the new Kestrel Facilities logo

Target Market(s)

Professional

Industry/Entity Type

Professional services

Contact Information for Business Card

Employee name, title, phone number, email address, corporate office address and logo.

Font styles to use
Sans Serif

Colors
0054AA
0677BA
7BADD7
CADEEF
E8F1F8

Requirements
Must have
• My logo
Should not have
• any other pictures or images besides my logo

```html
<!DOCTYPE html>
<html lang="en">
<head>
<meta charset="utf-8">
<title>Kestrel Facilities – Business Card</title>
<link href="https://fonts.googleapis.com/css2?family=Josefin+Sans:wght@400;600&family=Montserrat:wght@700&display=swap" rel="stylesheet">
<style>
  :root {
    --brand-blue: #3577bf;
    --deep-blue: #0054aa;
    --ink: #1c1c1c;
    --swoosh-grey: #333333;
    --card-white: #ffffff;
    --backdrop: #e6e8eb;
  }
  * { box-sizing: border-box; margin: 0; padding: 0; }
  html, body { width: 1200px; height: 960px; overflow: hidden; }
  body {
    background: var(--backdrop);
    font-family: "Josefin Sans", Arial, sans-serif;
    color: var(--ink);
    position: relative;
  }
  .card {
    position: absolute;
    left: 250px;
    width: 700px;
    height: 400px;
    background: var(--card-white);
    border-radius: 22px;
    overflow: hidden;
    box-shadow: 0 6px 18px rgba(0,0,0,0.18);
  }
  .card--front { top: 60px; }
  .card--back { top: 500px; }

  .wordmark {
    display: flex;
    align-items: center;
    gap: 16px;
    color: var(--brand-blue);
    font-family: "Josefin Sans", Arial, sans-serif;
    font-weight: 600;
    text-transform: uppercase;
  }
  .wordmark__square {
    flex: none;
    background: var(--brand-blue);
  }
  .wordmark__name { line-height: 1.02; letter-spacing: 2px; }

  .card--front .wordmark {
    position: absolute;
    left: 50%; top: 50%;
    transform: translate(-50%, -50%);
  }
  .card--front .wordmark__square { width: 70px; height: 70px; }
  .card--front .wordmark__name { font-size: 46px; }

  .card--back .wordmark {
    position: absolute;
    left: 46px; top: 118px;
  }
  .card--back .wordmark__square { width: 52px; height: 52px; }
  .card--back .wordmark__name { font-size: 34px; }

  .divider {
    position: absolute;
    left: 332px; top: 50px;
    width: 1.5px; height: 210px;
    background: var(--brand-blue);
  }
  .contact {
    position: absolute;
    left: 362px; top: 52px;
  }
  .contact__name {
    font-family: "Montserrat", Arial, sans-serif;
    font-weight: 700;
    font-size: 24px;
    color: var(--brand-blue);
    letter-spacing: 0.5px;
  }
  .contact__title { font-size: 18px; margin-top: 2px; }
  .contact__address { font-size: 16px; line-height: 1.4; margin-top: 18px; }
  .contact__list { list-style: none; margin-top: 14px; }
  .contact__list li {
    display: flex; align-items: center; gap: 8px;
    font-size: 17px; line-height: 1.45;
  }
  .contact__list svg { width: 15px; height: 15px; fill: var(--brand-blue); flex: none; }

  .swoosh { position: absolute; left: 0; bottom: 0; width: 700px; height: 400px; }
</style>
</head>
<body>
  <section class="card card--front" aria-label="Card front">
    <div class="wordmark">
      <span class="wordmark__square"></span>
      <span class="wordmark__name">Kestrel<br>Facilities</span>
    </div>
  </section>

  <section class="card card--back" aria-label="Card back">
    <svg class="swoosh" viewBox="0 0 700 400" aria-hidden="true">
      <path d="M0,400 C180,385 420,330 700,250 L700,400 Z" fill="var(--brand-blue)"/>
      <path d="M130,388 C330,360 520,300 700,232" fill="none" stroke="var(--swoosh-grey)" stroke-width="7"/>
    </svg>

    <div class="wordmark">
      <span class="wordmark__square"></span>
      <span class="wordmark__name">Kestrel<br>Facilities</span>
    </div>

    <div class="divider"></div>

    <div class="contact">
      <p class="contact__name">AMARA WEKESA</p>
      <p class="contact__title">Co-Founder</p>
      <p class="contact__address">P.O Box 4410-00100<br>Nairobi, Kenya</p>
      <ul class="contact__list">
        <li><svg viewBox="0 0 16 16"><path d="M3 1l3 3-2 2c1 2 3 4 5 5l2-2 3 3-2 3C6 15 1 10 1 3z"/></svg>+254-700-41822</li>
        <li><svg viewBox="0 0 16 16"><path d="M1 3h14v10H1z M2 4l6 5 6-5" stroke="#fff" stroke-width="1"/></svg>info@kestrelfm.com</li>
        <li><svg viewBox="0 0 16 16"><circle cx="8" cy="8" r="7"/><path d="M1 8h14M8 1c3 3 3 11 0 14M8 1c-3 3-3 11 0 14" stroke="#fff" stroke-width="1" fill="none"/></svg>www.kestrelfm.com</li>
      </ul>
    </div>
  </section>
</body>
</html>
```